QHX Compliant Dietary Supplement Label for Nutritional Company

We are in need of a label for our line of 20+ dietary supplements that are specifically formulated to balance body chemistry and match the biochemical individuality of our users based on hair tissue mineral analysis.

We have a line of approximately 20 different dietary supplements that will require use of new label in both a small (90 capsule) and large (180 capsule) size. We will start with the initial label in which Product name, Supplement Facts, and Ingredient list will need to be modified for each particular product thereafter.

The label will be placed on a transparent blue bottle with the color of lid being decided after label design. We are open to a transparent light amber bottle with black lid but blue is our preference.

We would like the majority of the label to be blue. Solid blue, fading of blue to darker blue/black, or subtle background designs are welcome with involvement of white and hints of orange. We do not want pictorial images on the label.

Label size:
Small bottle (120cc): Label size ~ 2.25” x 5.875”
Large bottle (200cc): Label size ~ 2.75” x 7.625”

Front:
-Logo near top of label with product name and description in middle and capsule count near the bottom

Right Side:
-Supplement Facts: See current product image below in brief
-Ingredient list: See current product image below in brief
-Manufactured for: See image below (This is on the left side of our current bottle and would like it moved to the bottom of the right side)

Left side:
-Suggested use: See current product image below in brief
-Leave room for possible warning statement
-Leave room for possible lot number printing
-Keep out of the reach of children.

The first files below are our current supplement label with product information. This information is what is needed on the label and will likely need some adjustments as we are updating our line of supplements and changes in QHX requirements.

The following files are the logo files and color palette.

The remaining files are some designs we came across for inspiration.

Thank you.

Target Market(s)

Health Care Profressionals

Industry/Entity Type

Health Care and Nutrition

Requirements
Nice to have
• Product name needs to be on same line in all one color
Should not have
• Pictorial Images

```html
<!DOCTYPE html>
<html lang="en">
<head>
<meta charset="utf-8">
<title>Vitaron Supplement Labels</title>
<link href="https://fonts.googleapis.com/css2?family=Lato:wght@400;700;900&family=Montserrat:wght@400;500&display=swap" rel="stylesheet">
<style>
  :root{
    --navy:#19245a;
    --blue-mid:#1b3c84;
    --blue-low:#1d5cb3;
    --orange:#f47b20;
    --frame:rgba(120,170,235,.55);
    --logo-blue:#4f86d6;
    --white:#ffffff;
    --page:#ffffff;
  }
  *{box-sizing:border-box;margin:0;padding:0}
  html,body{width:1200px;height:906px;overflow:hidden;background:var(--page)}
  .sheet{position:relative;width:1200px;height:906px}

  .label{
    position:absolute;overflow:hidden;color:var(--white);
    font-family:"Lato",sans-serif;
    background:linear-gradient(180deg,var(--navy) 0%,var(--blue-mid) 55%,var(--blue-low) 100%);
    box-shadow:3px 4px 6px rgba(0,0,0,.25);
  }
  .label--small{left:160px;top:58px;width:880px;height:340px;font-size:8.8px}
  .label--large{left:50px;top:448px;width:1100px;height:400px;font-size:11px}

  .label__rule{position:absolute;left:0;right:0;top:2.3em;height:.2em;background:var(--orange)}
  .label__band{position:absolute;left:0;right:0;bottom:0;height:2em;background:var(--orange)}
  .label__frame{position:absolute;top:1.2em;left:1.2em;right:1.2em;bottom:2.1em;border:1px solid var(--frame)}

  .label__body{
    position:absolute;top:4.2em;bottom:3.4em;left:4.2em;right:3.6em;
    display:grid;grid-template-columns:27fr 40fr 27fr;column-gap:3.6em;
  }

  /* left panel */
  .directions{display:flex;flex-direction:column;font-size:.95em;line-height:1.38}
  .directions p{text-align:justify;margin-bottom:1.1em}
  .directions b{font-weight:700}
  .disclaimer{
    margin-top:auto;border:1px solid var(--white);border-radius:.3em;
    padding:.5em .6em;font-size:.86em;line-height:1.3;text-align:justify;
  }
  .lot-box{margin-top:1.6em;height:5.4em;background:var(--white);border:1px solid var(--orange);border-radius:.25em}

  /* center panel */
  .front{display:flex;flex-direction:column;align-items:center;text-align:center}
  .brand{display:flex;flex-direction:column;align-items:center;color:var(--logo-blue);font-family:"Montserrat",sans-serif;font-weight:400;margin-top:2.2em}
  .brand__dot{width:2.2em;height:2.2em;border-radius:50%;background:var(--logo-blue);margin-bottom:.6em}
  .brand__name{font-size:2.6em;letter-spacing:.04em;line-height:1}
  .brand__sub{font-size:.95em;letter-spacing:.42em;margin-top:.35em}
  .product{font-family:"Lato",sans-serif;font-weight:900;font-size:5.4em;line-height:1;margin-top:.7em;letter-spacing:.01em}
  .descriptor{font-family:"Montserrat",sans-serif;font-weight:400;color:var(--orange);font-size:1.95em;line-height:1.25;margin-top:.45em}
  .count{margin-top:auto;align-self:flex-start;margin-left:-.5em;display:flex;align-items:center;gap:.5em}
  .count__num{display:flex;flex-direction:column;align-items:center;line-height:1}
  .count__num strong{font-family:"Montserrat",sans-serif;font-weight:500;font-size:2.2em}
  .count__num small{font-size:.45em;letter-spacing:.05em}
  .count__bar{width:1px;height:2.8em;background:var(--white)}
  .count__label{font-family:"Montserrat",sans-serif;font-size:1.3em;line-height:1.05;text-align:left}

  /* right panel */
  .facts-col{display:flex;flex-direction:column;font-size:.95em}
  .facts{border:1px solid var(--white);border-radius:.2em;padding:.5em .7em .4em}
  .facts__title{font-weight:900;font-size:2.2em;line-height:1.05}
  .facts__serving{font-weight:700;font-size:.9em;line-height:1.25;padding-bottom:.4em;border-bottom:.35em solid var(--white)}
  .facts table{width:100%;border-collapse:collapse;font-size:.88em}
  .facts th{font-weight:700;font-size:.9em;text-align:right;line-height:1.15;padding:.5em 0 .3em}
  .facts th:last-child,.facts td:last-child{width:3.8em}
  .facts td{padding:.35em 0 .25em;vertical-align:bottom;line-height:1.2}
  .facts td.num{text-align:right;white-space:nowrap}
  .facts thead tr{border-bottom:.2em solid var(--white)}
  .facts tbody tr{border-bottom:1px solid var(--white)}
  .facts tbody tr:last-child{border-bottom:.3em solid var(--white)}
  .facts .indent{display:block;padding-left:1em}
  .facts__note{font-size:.85em;padding-top:.3em}
  .ingredients{margin-top:1.1em;line-height:1.3}
  .distributor{margin-top:auto;line-height:1.3}
</style>
</head>
<body>
<main class="sheet">

  <section class="label label--small" aria-label="Small bottle label">
    <div class="label__rule"></div>
    <div class="label__frame"></div>
    <div class="label__band"></div>
    <div class="label__body">
      <div class="directions">
        <p><b>SUGGESTED USE:</b> As a dietary supplement, take one (1) capsule daily or as recommended by a healthcare practitioner.</p>
        <p><b>NOTICE:</b> It is advisable to keep this and all supplements out of the reach of children.</p>
        <div class="disclaimer">* These statements have not been evaluated by the QHX. This product is not intended to diagnose, treat, cure, or prevent any disease.</div>
        <div class="lot-box"></div>
      </div>
      <div class="front">
        <div class="brand"><span class="brand__dot"></span><span class="brand__name">KERALYN</span><span class="brand__sub">LABORATORIES</span></div>
        <h1 class="product">VITARON</h1>
        <p class="descriptor">MULTIPLE VITAMIN &amp;<br>MINERAL SUPPLEMENT</p>
        <div class="count"><span class="count__num"><strong>90</strong><small>CAPSULES</small></span><span class="count__bar"></span><span class="count__label">DIETARY<br>SUPPLEMENT</span></div>
      </div>
      <div class="facts-col">
        <div class="facts">
          <div class="facts__title">Supplement Facts</div>
          <div class="facts__serving">Serving Size: 1 Capsule<br>Servings Per Container: 90</div>
          <table>
            <thead><tr><th></th><th>Amount Per Serving</th><th>% Daily Value †</th></tr></thead>
            <tbody>
              <tr><td>Vitamin D (as cholecalciferol)</td><td class="num">1,662 mcg</td><td class="num">8.3%</td></tr>
              <tr><td>Calcium Complex (as calcium amino<span class="indent">acid chelate, dicalcium malate)</span></td><td class="num">100 mg</td><td class="num">7.7%</td></tr>
              <tr><td>Magnesium Complex (as magnesium<span class="indent">amino acid chelate, dimagnesium malate)</span></td><td class="num">60 mg</td><td class="num">14.3%</td></tr>
              <tr><td>Boron (as boron glycinate<span class="indent">(Boroplex™))</span></td><td class="num">250 mcg</td><td class="num">†</td></tr>
            </tbody>
          </table>
          <div class="facts__note">† Daily Value not established</div>
        </div>
        <p class="ingredients"><b>Other Ingredients:</b> Hypromellose (Vegetable Capsule)</p>
        <p class="distributor"><b>Distributed by:</b> KERALYN LABORATORIES, INC.<br>Mesa Ridge, AZ 85000 USA</p>
      </div>
    </div>
  </section>

  <section class="label label--large" aria-label="Large bottle label">
    <div class="label__rule"></div>
    <div class="label__frame"></div>
    <div class="label__band"></div>
    <div class="label__body">
      <div class="directions">
        <p><b>SUGGESTED USE:</b> As a dietary supplement, take one (1) capsule daily or as recommended by a healthcare practitioner.</p>
        <p><b>NOTICE:</b> It is advisable to keep this and all supplements out of the reach of children.</p>
        <div class="disclaimer">* These statements have not been evaluated by the QHX. This product is not intended to diagnose, treat, cure, or prevent any disease.</div>
        <div class="lot-box"></div>
      </div>
      <div class="front">
        <div class="brand"><span class="brand__dot"></span><span class="brand__name">KERALYN</span><span class="brand__sub">LABORATORIES</span></div>
        <h1 class="product">VITARON</h1>
        <p class="descriptor">MULTIPLE VITAMIN &amp;<br>MINERAL SUPPLEMENT</p>
        <div class="count"><span class="count__num"><strong>90</strong><small>CAPSULES</small></span><span class="count__bar"></span><span class="count__label">DIETARY<br>SUPPLEMENT</span></div>
      </div>
      <div class="facts-col">
        <div class="facts">
          <div class="facts__title">Supplement Facts</div>
          <div class="facts__serving">Serving Size: 1 Capsule<br>Servings Per Container: 90</div>
          <table>
            <thead><tr><th></th><th>Amount Per Serving</th><th>% Daily Value †</th></tr></thead>
            <tbody>
              <tr><td>Vitamin D (as cholecalciferol)</td><td class="num">1,662 mcg</td><td class="num">8.3%</td></tr>
              <tr><td>Calcium Complex (as calcium amino<span class="indent">acid chelate, dicalcium malate)</span></td><td class="num">100 mg</td><td class="num">7.7%</td></tr>
              <tr><td>Magnesium Complex (as magnesium<span class="indent">amino acid chelate, dimagnesium malate)</span></td><td class="num">60 mg</td><td class="num">14.3%</td></tr>
              <tr><td>Boron (as boron glycinate<span class="indent">(Boroplex™))</span></td><td class="num">250 mcg</td><td class="num">†</td></tr>
            </tbody>
          </table>
          <div class="facts__note">† Daily Value not established</div>
        </div>
        <p class="ingredients"><b>Other Ingredients:</b> Hypromellose (Vegetable Capsule)</p>
        <p class="distributor"><b>Distributed by:</b> KERALYN LABORATORIES, INC.<br>Mesa Ridge, AZ 85000 USA</p>
      </div>
    </div>
  </section>

</main>
</body>
</html>
```